Moravel Aesthetic Doctor

I require an elegant, luxurious looking business card for my aesthetic business. I am a doctor and that will set me aside from competitors. I am planning to provide home and spa based treatments to clients with high expectations. I have attached my logo.

```html
<!DOCTYPE html>
<html lang="en">
<head>
<meta charset="utf-8">
<title>Moravel Aesthetic Doctor — Business Card</title>
<link href="https://fonts.googleapis.com/css2?family=Marcellus&family=Roboto:wght@300;400&display=swap" rel="stylesheet">
<style>
  :root {
    --backdrop: #3b3b3d;
    --card: #1c1d1f;
    --card-edge: #26272a;
    --sky: #4fb3e8;
    --silver: #c9ccd1;
    --muted: #9a9ea5;
    --rule: #6d7178;
  }
  * { margin: 0; padding: 0; box-sizing: border-box; }
  html, body { width: 799px; height: 1200px; overflow: hidden; }
  body {
    background: var(--backdrop);
    position: relative;
    font-family: "Roboto", sans-serif;
  }
  .card {
    position: absolute;
    left: 80px;
    width: 640px;
    height: 366px;
    background: var(--card);
    border: 1px solid var(--card-edge);
    border-radius: 4px;
    overflow: hidden;
    box-shadow: 0 18px 40px rgba(0,0,0,.45);
  }
  .card--front { top: 120px; }
  .card--back { top: 715px; }

  /* Front */
  .front-mark {
    position: absolute;
    inset: 0;
    display: flex;
    align-items: center;
    justify-content: center;
    gap: 16px;
  }
  .front-mark__dot {
    width: 34px; height: 34px;
    border-radius: 50%;
    border: 2px solid var(--silver);
  }
  .front-mark__name {
    font-family: "Marcellus", serif;
    color: var(--silver);
    font-size: 30px;
    letter-spacing: 3px;
    text-transform: uppercase;
  }

  /* Back */
  .side-band {
    position: absolute;
    left: 0; top: 0; bottom: 0;
    width: 34px;
    background: var(--sky);
  }
  .side-rule {
    position: absolute;
    left: 42px; top: 0; bottom: 0;
    width: 3px;
    background: var(--rule);
  }
  .brand {
    position: absolute;
    left: 82px; top: 48px;
    display: flex;
    align-items: center;
    gap: 16px;
  }
  .brand__dot {
    width: 54px; height: 54px;
    border-radius: 50%;
    border: 2px solid var(--silver);
  }
  .brand__name {
    font-family: "Marcellus", serif;
    color: var(--silver);
    font-size: 38px;
    line-height: 1.05;
    letter-spacing: 2px;
    text-transform: uppercase;
  }
  .brand__name span { display: block; font-size: 22px; letter-spacing: 3px; }

  .person {
    position: absolute;
    left: 82px; top: 180px;
  }
  .person__name {
    color: var(--muted);
    font-weight: 300;
    font-size: 22px;
  }
  .person__name small {
    font-size: 11px;
    color: var(--sky);
    margin-left: 6px;
  }
  .person__title {
    color: var(--sky);
    font-size: 14px;
    margin-top: 3px;
  }
  .divider {
    position: absolute;
    left: 82px; right: 70px; top: 246px;
    height: 1px;
    background: var(--rule);
  }
  .contacts {
    position: absolute;
    left: 82px; top: 262px;
    display: flex;
    gap: 26px;
    color: var(--silver);
    font-size: 14px;
  }
  .contact { display: flex; align-items: center; gap: 8px; }
  .contact svg { width: 18px; height: 18px; }
  .web {
    position: absolute;
    left: 330px; top: 300px;
    color: var(--silver);
    font-size: 14px;
    display: flex; align-items: center; gap: 8px;
  }
  .web svg { width: 18px; height: 18px; }
  .foot-band {
    position: absolute;
    right: 0; bottom: 34px;
    width: 150px; height: 20px;
    background: var(--sky);
  }
  .social {
    position: absolute;
    right: 82px; bottom: 48px;
    width: 64px; height: 26px;
    background: var(--sky);
    border-radius: 13px;
    display: flex; align-items: center; justify-content: center; gap: 8px;
  }
  .social__dot { width: 14px; height: 14px; border-radius: 50%; background: #fff; }
</style>
</head>
<body>
  <section class="card card--front" aria-label="Card front">
    <div class="front-mark">
      <div class="front-mark__dot"></div>
      <div class="front-mark__name">Moravel</div>
    </div>
  </section>

  <section class="card card--back" aria-label="Card back">
    <div class="side-band"></div>
    <div class="side-rule"></div>

    <div class="brand">
      <div class="brand__dot"></div>
      <div class="brand__name">Moravel<span>Aesthetic Doctor</span></div>
    </div>

    <div class="person">
      <div class="person__name">Dr Elise Varro<small>MRCPCH MD</small></div>
      <div class="person__title">Australasian Diploma of Aesthetic Medicine</div>
    </div>

    <div class="divider"></div>

    <div class="contacts">
      <div class="contact">
        <svg viewBox="0 0 24 24" fill="none" stroke="currentColor" stroke-width="1.6"><circle cx="12" cy="12" r="10.5"/><path d="M8.5 7.5c.6-.6 1.4-.5 1.8.1l.9 1.4c.3.5.2 1.1-.2 1.5l-.6.5c.6 1.3 1.6 2.3 2.9 2.9l.5-.6c.4-.4 1-.5 1.5-.2l1.4.9c.6.4.7 1.2.1 1.8-1 1-2.6 1.1-3.9.3-2-1.2-3.5-2.7-4.7-4.7-.8-1.3-.7-2.9.3-3.9z" fill="currentColor" stroke="none"/></svg>
        0800 555 014
      </div>
      <div class="contact">
        <svg viewBox="0 0 24 24" fill="none" stroke="currentColor" stroke-width="1.6"><circle cx="12" cy="12" r="10.5"/><rect x="6.5" y="8" width="11" height="8" rx="1"/><path d="M6.5 8.5l5.5 4 5.5-4"/></svg>
        elise@moravel.co.nz
      </div>
    </div>
    <div class="web">
      <svg viewBox="0 0 24 24" fill="none" stroke="currentColor" stroke-width="1.4"><circle cx="12" cy="12" r="10.5"/><ellipse cx="12" cy="12" rx="4" ry="8"/><path d="M4 12h16M5.5 8h13M5.5 16h13"/></svg>
      www.moravel.co.nz
    </div>

    <div class="foot-band"></div>
    <div class="social" aria-label="Social links">
      <div class="social__dot"></div>
      <div class="social__dot"></div>
    </div>
  </section>
</body>
</html>
```